Company Flyer for Electric boating company

I am looking for a company flyer which we can hand over to boat owners in the Netherlands (Amsterdam area). Our core business is to rebuild every boat (from 4 to 10 meters) into an electrically propelled boat. We are taking out diesels and replace them with a high quality electrical motor, inboard varying from 30 till 80 pk (hp). And outboard from 1pk (hp) till 200pk. We are the best, not the cheapest, not the most expensive. We only work with the best materials. The flyer has to be sort of in line with our website and branding.

Major advantages of electric boating are:
- completely silent
- no fumes, smells or smoke
- cheap to operate
- environmentally friendly
- obliged in more and more areas
- no maintenance
- more enjoyable

The flyer should be A5 format. Since all the text has to be in Dutch I expect only the graphical design and layout for advantages, process, pricing and contact details etc.

Target Market(s)

Boat owners in the Netherlands

Font styles to use
Sans Serif

Colors
9bcb3c
add136
cadf82
0555a3
3176b5
85acd3
e0ebf3

Requirements
Must have
• Clean design, in line with website: www.volthaven.nl
Nice to have
• icons for advantages, boating etc

2 sides
Should not have
• Steering wheel...

```html
<!DOCTYPE html>
<html lang="nl">
<head>
<meta charset="utf-8">
<title>Volthaven – Electric Boating flyer</title>
<link rel="stylesheet" href="https://fonts.googleapis.com/css2?family=Bebas+Neue&family=Montserrat:wght@400;500;600;700&display=swap">
<style>
  :root {
    --navy: #0c3c76;
    --navy-deep: #082c5a;
    --sea: #1b5a9c;
    --green: #82c41f;
    --green-soft: #cadf82;
    --ink: #1d1d1f;
    --grey-text: #3a3a3a;
    --paper: #ffffff;
    --backdrop: #efefef;
    --buoy-red: #e2452b;
    --buoy-light: #f3b3a6;
  }
  * { margin: 0; padding: 0; box-sizing: border-box; }
  html, body { width: 783px; height: 1200px; overflow: hidden; background: var(--backdrop); }
  body { position: relative; font-family: "Montserrat", sans-serif; }

  .page {
    position: absolute; top: 344px; width: 361px; height: 512px; overflow: hidden;
    box-shadow: 0 3px 10px rgba(0,0,0,.25);
  }
  .page--front { left: 20px; background: var(--navy); }
  .page--back { left: 402px; background: var(--paper); }

  /* front */
  .sea-photo {
    position: absolute; inset: 0;
    background: radial-gradient(ellipse at 40% 30%, var(--sea) 0%, var(--navy) 55%, var(--navy-deep) 100%);
  }
  .boat-photo {
    position: absolute; left: 0; top: 210px; width: 185px; height: 290px;
    background: radial-gradient(ellipse at 45% 55%, #f4f4f2 0%, #d8dee4 35%, rgba(200,215,230,.55) 60%, rgba(12,60,118,0) 78%);
  }
  .brand { position: absolute; display: flex; align-items: center; gap: 7px; }
  .brand__dot { border-radius: 50%; background: var(--green); }
  .brand__name { font-weight: 700; color: var(--green); letter-spacing: .5px; }
  .page--front .brand { left: 38px; top: 26px; }
  .page--front .brand__dot { width: 26px; height: 26px; }
  .page--front .brand__name { font-size: 18px; }

  .headline { position: absolute; left: 38px; font-family: "Bebas Neue", sans-serif; line-height: 1; }
  .headline--electric { top: 70px; font-size: 62px; color: #fff; letter-spacing: 1px; }
  .headline--boating { top: 122px; font-size: 96px; color: var(--green); display: flex; align-items: center; letter-spacing: 1px; }
  .lifebuoy-photo {
    width: 64px; height: 66px; margin: 0 4px 8px 2px;
    background: linear-gradient(135deg, var(--buoy-light) 0%, var(--buoy-red) 100%);
  }

  .advantages { position: absolute; left: 195px; top: 222px; width: 160px; }
  .advantages__title { font-size: 10.3px; font-weight: 700; color: var(--green); line-height: 1.25; }
  .advantages__rule { width: 35px; height: 1.5px; background: var(--green); margin: 8px 0 11px; }
  .advantages__list { list-style: none; }
  .advantages__item {
    display: flex; gap: 7px; align-items: flex-start;
    font-size: 8.6px; font-weight: 500; color: #fff; line-height: 1.2; margin-bottom: 4.5px;
  }
  .advantages__item--gap { margin-top: 6px; }
  .tick { width: 10px; height: 10px; flex: none; }

  .contact-band {
    position: absolute; bottom: 12px; left: 16px; right: 0; height: 18px;
    background: var(--green); clip-path: polygon(10px 0, 100% 0, 100% 100%, 0 100%);
    display: flex; align-items: center; justify-content: center; gap: 7px;
    font-size: 9px; color: #fff; white-space: nowrap;
  }
  .contact-band__sep { opacity: .8; }
  .contact-band svg { width: 8px; height: 8px; margin-right: 3px; vertical-align: -1px; }

  /* back */
  .header-photo {
    position: absolute; left: 0; top: 9px; width: 361px; height: 96px;
    background: linear-gradient(90deg, #fff 0%, #fff 28%, #dce8f2 50%, #7fa9cf 80%, #4f86bb 100%);
  }
  .page--back .brand { left: 20px; top: 18px; }
  .page--back .brand__dot { width: 18px; height: 18px; }
  .page--back .brand__name { font-size: 11px; }
  .intro-title { position: absolute; left: 20px; top: 45px; font-size: 10px; font-weight: 700; color: var(--green); line-height: 1.22; }
  .intro-sub { position: absolute; left: 20px; top: 79px; font-size: 7.3px; font-weight: 600; color: var(--ink); line-height: 1.3; }
  .header-rule { position: absolute; left: 0; right: 0; top: 106px; height: 2px; background: var(--green); }

  .timeline { position: absolute; inset: 0; pointer-events: none; }
  .step-icon { position: absolute; width: 21px; height: 21px; }
  .step-title { position: absolute; font-size: 8px; font-weight: 700; color: var(--ink); letter-spacing: .3px; white-space: nowrap; }
  .step-text { position: absolute; font-size: 4.6px; line-height: 1.3; color: var(--grey-text); text-align: justify; }
  .step-text--right { text-align-last: right; }

  .pricing-title { position: absolute; left: 20px; top: 372px; font-size: 8.3px; font-weight: 700; color: var(--green); }
  .price { position: absolute; top: 396px; width: 80px; margin-left: -40px; text-align: center; }
  .price__hull { width: 46px; height: 18px; display: block; margin: 0 auto; }
  .price__name { margin-top: 6px; font-size: 6px; font-weight: 700; color: var(--green); }
  .price__size { font-size: 4.6px; font-weight: 700; color: var(--ink); line-height: 1.25; min-height: 12px; }
  .price__box {
    margin: 3px auto 0; width: 56px; height: 24px; background: var(--green); color: #fff;
    display: flex; flex-direction: column; align-items: center; justify-content: center;
  }
  .price__from { font-size: 4.5px; font-style: italic; line-height: 1; }
  .price__amount { font-size: 11.5px; font-weight: 700; line-height: 1.05; }
  .price__box--wide { width: 72px; font-size: 7px; font-weight: 700; }
</style>
</head>
<body>

<!-- FRONT -->
<section class="page page--front">
  <div class="sea-photo" role="img" aria-label="Open blue sea surface seen from above"></div>
  <div class="boat-photo" role="img" aria-label="White motor yacht seen from above cruising with a foamy wake"></div>

  <div class="brand"><span class="brand__dot"></span><span class="brand__name">VOLTHAVEN</span></div>

  <h1 class="headline headline--electric">ELECTRIC</h1>
  <div class="headline headline--boating">
    <span>B</span><span class="lifebuoy-photo" role="img" aria-label="Photo of a red and white lifebuoy standing in for the letter O"></span><span>ATING</span>
  </div>

  <div class="advantages">
    <h2 class="advantages__title">MAJOR ADVANTAGES OF<br>ELECTRIC BOATING</h2>
    <div class="advantages__rule"></div>
    <ul class="advantages__list">
      <li class="advantages__item"><svg class="tick" viewBox="0 0 10 10"><circle cx="5" cy="5" r="4.3" fill="none" stroke="#82c41f" stroke-width=".9"/><path d="M2.8 5.1l1.6 1.6 3.6-3.8" fill="none" stroke="#82c41f" stroke-width=".9"/></svg>Completely silent</li>
      <li class="advantages__item"><svg class="tick" viewBox="0 0 10 10"><circle cx="5" cy="5" r="4.3" fill="none" stroke="#82c41f" stroke-width=".9"/><path d="M2.8 5.1l1.6 1.6 3.6-3.8" fill="none" stroke="#82c41f" stroke-width=".9"/></svg>No fumes, smells or smoke</li>
      <li class="advantages__item"><svg class="tick" viewBox="0 0 10 10"><circle cx="5" cy="5" r="4.3" fill="none" stroke="#82c41f" stroke-width=".9"/><path d="M2.8 5.1l1.6 1.6 3.6-3.8" fill="none" stroke="#82c41f" stroke-width=".9"/></svg>Cheap to operate</li>
      <li class="advantages__item"><svg class="tick" viewBox="0 0 10 10"><circle cx="5" cy="5" r="4.3" fill="none" stroke="#82c41f" stroke-width=".9"/><path d="M2.8 5.1l1.6 1.6 3.6-3.8" fill="none" stroke="#82c41f" stroke-width=".9"/></svg>Environmentally friendly</li>
      <li class="advantages__item advantages__item--gap"><svg class="tick" viewBox="0 0 10 10"><circle cx="5" cy="5" r="4.3" fill="none" stroke="#82c41f" stroke-width=".9"/><path d="M2.8 5.1l1.6 1.6 3.6-3.8" fill="none" stroke="#82c41f" stroke-width=".9"/></svg>Obliged in more and<br>more areas</li>
      <li class="advantages__item advantages__item--gap"><svg class="tick" viewBox="0 0 10 10"><circle cx="5" cy="5" r="4.3" fill="none" stroke="#82c41f" stroke-width=".9"/><path d="M2.8 5.1l1.6 1.6 3.6-3.8" fill="none" stroke="#82c41f" stroke-width=".9"/></svg>No maintenance</li>
      <li class="advantages__item"><svg class="tick" viewBox="0 0 10 10"><circle cx="5" cy="5" r="4.3" fill="none" stroke="#82c41f" stroke-width=".9"/><path d="M2.8 5.1l1.6 1.6 3.6-3.8" fill="none" stroke="#82c41f" stroke-width=".9"/></svg>More enjoyable</li>
    </ul>
  </div>

  <div class="contact-band">
    <span><svg viewBox="0 0 10 10"><path d="M2 1l2 2-1 1.3c.6 1.3 1.5 2.2 2.7 2.7L7 6l2 2-1.3 1.5C4.5 9.3.7 5.5.5 2.3z" fill="#fff"/></svg>+31 6 12 480 357</span>
    <span class="contact-band__sep">|</span>
    <span><svg viewBox="0 0 10 10"><rect x=".5" y="2" width="9" height="6" fill="#fff"/><path d="M.5 2l4.5 3.5L9.5 2" fill="none" stroke="#82c41f" stroke-width=".8"/></svg>info@volthaven.nl</span>
    <span class="contact-band__sep">|</span>
    <span><svg viewBox="0 0 10 10"><circle cx="5" cy="5" r="4.2" fill="none" stroke="#fff"/><path d="M1 5h8M5 .8c-2.4 2.6-2.4 5.8 0 8.4M5 .8c2.4 2.6 2.4 5.8 0 8.4" fill="none" stroke="#fff" stroke-width=".7"/></svg>www.volthaven.nl</span>
  </div>
</section>

<!-- BACK -->
<section class="page page--back">
  <div class="header-photo" role="img" aria-label="White motor yacht speeding across a calm blue bay"></div>
  <div class="brand"><span class="brand__dot"></span><span class="brand__name">VOLTHAVEN</span></div>
  <h2 class="intro-title">HOE WERKT HET ELEKTRISCH<br>OMBOUWEN VAN EEN BOOT?</h2>
  <p class="intro-sub">Het Ombouwen Van Jouw Boot Is Een<br>Project Waar Wij Je Graag Bij Betrekken</p>
  <div class="header-rule"></div>

  <svg class="timeline" viewBox="0 0 361 512">
    <g fill="none" stroke="#555" stroke-width=".6" stroke-dasharray="2 1.5">
      <path d="M31 136V165H207"/>
      <path d="M327 177V212H104"/>
      <path d="M31 223V246H253"/>
      <path d="M327 257V284H145"/>
      <path d="M31 295V333H198"/>
    </g>
    <g fill="#82c41f">
      <circle cx="207" cy="165" r="1.6"/>
      <circle cx="104" cy="212" r="1.6"/>
      <circle cx="253" cy="246" r="1.6"/>
      <circle cx="145" cy="284" r="1.6"/>
      <circle cx="198" cy="333" r="1.6"/>
    </g>
  </svg>

  <svg class="step-icon" style="left:21px;top:115px" viewBox="0 0 21 21"><circle cx="10.5" cy="10.5" r="9.8" fill="none" stroke="#444" stroke-width=".6" stroke-dasharray="1.5 1"/><path d="M5.5 10a5 3.8 0 1 1 3 3.4L6 15l.6-2.4A3.6 3.6 0 0 1 5.5 10z" fill="none" stroke="#82c41f" stroke-width=".8"/></svg>
  <svg class="step-icon" style="left:316px;top:155px" viewBox="0 0 21 21"><circle cx="10.5" cy="10.5" r="9.8" fill="none" stroke="#444" stroke-width=".6" stroke-dasharray="1.5 1"/><circle cx="7.5" cy="12" r="2.6" fill="none" stroke="#82c41f" stroke-width=".8"/><circle cx="13.5" cy="12" r="2.6" fill="none" stroke="#82c41f" stroke-width=".8"/><path d="M6 9.5l1-3.5h2l1 3.5M11 9.5l1-3.5h2l1 3.5" fill="none" stroke="#82c41f" stroke-width=".8"/></svg>
  <svg class="step-icon" style="left:21px;top:202px" viewBox="0 0 21 21"><circle cx="10.5" cy="10.5" r="9.8" fill="none" stroke="#444" stroke-width=".6" stroke-dasharray="1.5 1"/><path d="M6 15l8-8M13 5.5a2 2 0 1 0 2.5 2.5M6 6l9 9" fill="none" stroke="#82c41f" stroke-width=".9"/></svg>
  <svg class="step-icon" style="left:316px;top:236px" viewBox="0 0 21 21"><circle cx="10.5" cy="10.5" r="9.8" fill="none" stroke="#444" stroke-width=".6" stroke-dasharray="1.5 1"/><rect x="7.5" y="6" width="6" height="10" rx=".8" fill="none" stroke="#82c41f" stroke-width=".8"/><path d="M9.5 5h2M11 8l-2 3h2.5l-2 3" fill="none" stroke="#82c41f" stroke-width=".7"/></svg>
  <svg class="step-icon" style="left:21px;top:274px" viewBox="0 0 21 21"><circle cx="10.5" cy="10.5" r="9.8" fill="none" stroke="#444" stroke-width=".6" stroke-dasharray="1.5 1"/><rect x="6" y="6" width="9" height="10" fill="none" stroke="#82c41f" stroke-width=".8"/><path d="M7 12h2l1-3 1.5 5 1-2H14" fill="none" stroke="#82c41f" stroke-width=".7"/></svg>
  <svg class="step-icon" style="left:316px;top:323px" viewBox="0 0 21 21"><circle cx="10.5" cy="10.5" r="9.8" fill="none" stroke="#444" stroke-width=".6" stroke-dasharray="1.5 1"/><path d="M7 14l2-5 6-4-4 6zM7 14l-1.5 1.5M9 13l-1 2.5" fill="none" stroke="#82c41f" stroke-width=".8"/></svg>

  <h3 class="step-title" style="left:48px;top:118px">KENNISMAKING</h3>
  <p class="step-text" style="left:48px;top:129px;width:289px">Allereerst zullen wij tot een volledige analyse komen van je boot om vervolgens een volledig advies uit te brengen over de wenselijke en mogelijke activiteiten; eventueel in een meer fasen plan. Nadat wij samen met jou een plan hebben gemaakt, krijg je van ons een offerte waarin precies is aangegeven welke zaken door ons worden aangepakt. Alles volgens de meest actuele veiligheids- en kwaliteits normen.</p>

  <h3 class="step-title" style="right:50px;top:161px">PLANNING EN START VAN HET PROJECT</h3>
  <p class="step-text step-text--right" style="left:22px;top:174px;width:290px">Allereerst zullen wij tot een volledige analyse komen van je boot om vervolgens een volledig advies uit te brengen over de wenselijke en mogelijke activiteiten; eventueel in een meer fasen plan. Nadat wij samen met jou een plan hebben gemaakt, krijg je van ons een offerte waarin precies is aangegeven welke zaken door ons worden aangepakt. Alles volgens de meest actuele veiligheids- en kwaliteits normen.</p>

  <h3 class="step-title" style="left:48px;top:208px">OUD ERUIT</h3>
  <p class="step-text" style="left:48px;top:220px;width:289px">Hierbij worden motor, en eventuele aandrijvings componenten zoals bijv. schroef en schroefas verwijderd (wij hebben aandacht voor hergebruik en restwaarde) alsmede besturingselectronica en eventueel delen van het interieur.</p>

  <h3 class="step-title" style="right:50px;top:242px">NIEUW ERIN</h3>
  <p class="step-text step-text--right" style="left:22px;top:256px;width:290px">Hierbij wordt de nieuwe aandrijflijn ter plaatse gemonteerd. Eventuele ondersteuning wordt opnieuw, in eigen beheer, vervaardigd. Aanpassing op de schroefas wordt gerealiseerd. Besturingselectronica (grotendeels met de motor meegeleverd wordt opnieuw aangelegd.</p>

  <h3 class="step-title" style="left:48px;top:280px">TEST &amp; OVERDRACHT</h3>
  <p class="step-text" style="left:48px;top:292px;width:289px">Nadat de beoogde eindfase is bereikt vindt een uitvoerige testfase plaats waarna ons team eventueel kan adviseren tot aanvullende werkzaamheden. Dit laatste proberen wij echter zoveel mogelijk te vermijden om je de meest optimale transparantie te kunnen aanbieden. Wanneer de testprocedure succesvol is verlopen, is de boot kaar voor aflevering en kun je elektrisch gaan varen. Voor ons was dit een openbaring; wij zijn er zeker van dat jij dit ook zo zult ervaren!.</p>

  <h3 class="step-title" style="right:50px;top:329px">VAREN EN SERVICE</h3>
  <p class="step-text step-text--right" style="left:22px;top:341px;width:290px">Na een paar weken wil je niet anders meer en ben je volledig gewend aan het rustige gekabbel van de golfjes tegen je boot. Wij willen graag dan even de boot nog een keertje nakijken en waar nodig alles nog even aandraaien. Wanneer je verder nog punten van aandacht hebt dan kunnen wij hier ook meteen naar kijken.</p>

  <h2 class="pricing-title">PRIJZEN VOOR HET OMBOUWEN</h2>

  <div class="price" style="left:51px">
    <svg class="price__hull" viewBox="0 0 46 18"><path d="M1 4h44l-5 9H3z" fill="none" stroke="#333" stroke-width=".8"/><path d="M3 13v4h2" fill="none" stroke="#333" stroke-width=".8"/><rect x="5" y="6" width="5" height="3" fill="none" stroke="#333" stroke-width=".6"/></svg>
    <div class="price__name">KLEIN</div>
    <div class="price__size">TOT 5 MTR</div>
    <div class="price__box"><span class="price__from">vanaf</span><span class="price__amount">€2200,-</span></div>
  </div>
  <div class="price" style="left:130px">
    <svg class="price__hull" viewBox="0 0 46 18"><path d="M1 4h44l-5 9H3z" fill="none" stroke="#333" stroke-width=".8"/><path d="M3 13v4h2" fill="none" stroke="#333" stroke-width=".8"/><rect x="5" y="6" width="7" height="3" fill="none" stroke="#333" stroke-width=".6"/></svg>
    <div class="price__name">MIDDEL</div>
    <div class="price__size">5 MTR TOT 8,5 MTR</div>
    <div class="price__box"><span class="price__from">vanaf</span><span class="price__amount">€12500,-</span></div>
  </div>
  <div class="price" style="left:210px">
    <svg class="price__hull" viewBox="0 0 46 18"><path d="M1 4h44l-5 9H3z" fill="none" stroke="#333" stroke-width=".8"/><path d="M3 13v4h2" fill="none" stroke="#333" stroke-width=".8"/><rect x="5" y="6" width="9" height="3" fill="none" stroke="#333" stroke-width=".6"/></svg>
    <div class="price__name">GROOT</div>
    <div class="price__size">7 MTR TOT 10 MTR</div>
    <div class="price__box"><span class="price__from">vanaf</span><span class="price__amount">€17500,-</span></div>
  </div>
  <div class="price" style="left:298px">
    <svg class="price__hull" viewBox="0 0 46 18"><path d="M1 4h44l-5 9H3z" fill="none" stroke="#333" stroke-width=".8"/><path d="M3 13v4h2" fill="none" stroke="#333" stroke-width=".8"/><rect x="5" y="6" width="15" height="3" fill="none" stroke="#333" stroke-width=".6"/></svg>
    <div class="price__name">ANDERS</div>
    <div class="price__size">VANAF 10 METER OF<br>SNELVAREND</div>
    <div class="price__box price__box--wide">OP AANVRAAG</div>
  </div>

  <div class="contact-band">
    <span><svg viewBox="0 0 10 10"><path d="M2 1l2 2-1 1.3c.6 1.3 1.5 2.2 2.7 2.7L7 6l2 2-1.3 1.5C4.5 9.3.7 5.5.5 2.3z" fill="#fff"/></svg>+31 6 12 480 357</span>
    <span class="contact-band__sep">|</span>
    <span><svg viewBox="0 0 10 10"><rect x=".5" y="2" width="9" height="6" fill="#fff"/><path d="M.5 2l4.5 3.5L9.5 2" fill="none" stroke="#82c41f" stroke-width=".8"/></svg>info@volthaven.nl</span>
    <span class="contact-band__sep">|</span>
    <span><svg viewBox="0 0 10 10"><circle cx="5" cy="5" r="4.2" fill="none" stroke="#fff"/><path d="M1 5h8M5 .8c-2.4 2.6-2.4 5.8 0 8.4M5 .8c2.4 2.6 2.4 5.8 0 8.4" fill="none" stroke="#fff" stroke-width=".7"/></svg>www.volthaven.nl</span>
  </div>
</section>

</body>
</html>
```